KORV PTY LTD - Business Cards

Design a modern business card - using the attached Designs.
Same design as on the front, apart from the names/numbers/emails to be different.
We want the cards to be very glossy to stand out, do I think the simple black/white/metallic will be effective.
Both lots of details below:

Tom Wrenshaw
Director
tom_korv@nulvane.com
0438 274 093

Lewis Corbyn
Director
lewis_korv@nulvane.com
0419 385 642

Industry/Entity Type

Business

```html
<!DOCTYPE html>
<html lang="en">
<head>
<meta charset="utf-8">
<title>KORV PTY LTD – Business Cards</title>
<link rel="stylesheet" href="https://fonts.googleapis.com/css2?family=Bitter:wght@400;700&family=Open+Sans:wght@400&display=swap">
<style>
  :root {
    --page: #e6e4e1;
    --card-dark: #1c1c1c;
    --card-dark-edge: #0e0e0e;
    --metal-light: #d9dadb;
    --metal-mid: #9a9c9e;
    --metal-dark: #5e6062;
    --card-grey: #b4b4b4;
    --text-light: #f2f2f2;
    --text-soft: #d6d6d6;
    --rule: #8a8a8a;
    --mark-dark: #2a2a2a;
  }
  * { box-sizing: border-box; margin: 0; padding: 0; }
  html, body { width: 1200px; height: 468px; overflow: hidden; }
  body {
    background: var(--page);
    position: relative;
    font-family: "Open Sans", Arial, sans-serif;
  }
  .card {
    position: absolute;
    top: 84px;
    width: 520px;
    height: 300px;
    overflow: hidden;
    box-shadow: 0 6px 18px rgba(0,0,0,0.25);
  }
  .card--front { left: 50px; }
  .card--back { left: 630px; background: var(--card-grey); }

  .front-texture {
    position: absolute; inset: 0;
    background: radial-gradient(ellipse at 50% 45%, #2e2e2e 0%, var(--card-dark) 55%, var(--card-dark-edge) 100%);
  }
  .metal-band { position: absolute; left: 0; top: 0; width: 520px; height: 90px; }

  .brand {
    position: absolute;
    left: 0; right: 0;
    display: flex; align-items: center; justify-content: center; gap: 14px;
    font-family: "Bitter", Georgia, serif;
    font-weight: 700;
    letter-spacing: 6px;
  }
  .brand__dot { border-radius: 50%; flex: none; }
  .card--front .brand { top: 100px; font-size: 48px; color: var(--text-light); }
  .card--front .brand__dot { width: 22px; height: 22px; background: var(--metal-mid); }
  .card--back .brand { top: 0; bottom: 0; font-size: 72px; color: var(--mark-dark); }
  .card--back .brand__dot { width: 30px; height: 30px; background: var(--mark-dark); }

  .contact {
    position: absolute; left: 0; right: 0; top: 188px;
    text-align: center; color: var(--text-light);
  }
  .contact__name { font-family: "Bitter", Georgia, serif; font-weight: 700; font-size: 19px; }
  .contact__role { font-family: "Bitter", Georgia, serif; font-weight: 400; font-size: 16px; color: var(--text-soft); }
  .contact__rule { width: 190px; height: 1px; margin: 9px auto 12px; background: var(--rule); }
  .contact__line {
    display: flex; align-items: center; justify-content: center; gap: 7px;
    font-size: 16px; line-height: 24px; color: var(--text-light);
  }
  .contact__line svg { width: 13px; height: 13px; fill: var(--text-soft); }
</style>
</head>
<body>

<section class="card card--front" aria-label="Business card front">
  <div class="front-texture" role="img" aria-label="Dark perforated metal mesh background"></div>
  <svg class="metal-band" viewBox="0 0 520 90" aria-hidden="true">
    <defs>
      <linearGradient id="brushed" x1="0" y1="0" x2="1" y2="1">
        <stop offset="0" stop-color="var(--metal-dark)"/>
        <stop offset="0.35" stop-color="var(--metal-light)"/>
        <stop offset="0.6" stop-color="var(--metal-mid)"/>
        <stop offset="1" stop-color="var(--metal-light)"/>
      </linearGradient>
    </defs>
    <polygon points="0,0 520,0 520,22 440,22 410,50 140,50 110,82 0,82" fill="url(#brushed)"/>
    <polyline points="0,82 110,82 140,50 410,50 440,22 520,22" fill="none" stroke="#3a3a3a" stroke-width="2"/>
  </svg>

  <div class="brand"><span class="brand__dot"></span>KORV</div>

  <div class="contact">
    <p><span class="contact__name">Lewis Corbyn,</span> <span class="contact__role">Director</span></p>
    <div class="contact__rule"></div>
    <p class="contact__line">
      <svg viewBox="0 0 24 24" aria-hidden="true"><path d="M6.6 10.8a15.1 15.1 0 0 0 6.6 6.6l2.2-2.2c.3-.3.7-.4 1-.2 1.1.4 2.3.6 3.6.6.6 0 1 .4 1 1V20c0 .6-.4 1-1 1A17 17 0 0 1 3 4c0-.6.4-1 1-1h3.5c.6 0 1 .4 1 1 0 1.3.2 2.5.6 3.6.1.3 0 .7-.2 1z"/></svg>
      0419 385 642
    </p>
    <p class="contact__line">
      <svg viewBox="0 0 24 24" aria-hidden="true"><path d="M2 6h20v12H2z M2 6l10 7 10-7" fill="none" stroke="#d6d6d6" stroke-width="2"/></svg>
      lewis_korv@nulvane.com
    </p>
  </div>
</section>

<section class="card card--back" aria-label="Business card back">
  <div class="brand"><span class="brand__dot"></span>KORV</div>
</section>

</body>
</html>
```